Before the kettle boils, pocast with content in its majority of technology

Page dedicated to a pocast with content in its majority of technology. The page also contains the chapters of the podcast (pluggin Parlaveo) will also contain news. Preferably Worpress. There is already a very basic page with a simple theme, the logo and little more, I would like something more professional. Www.lamparadebolsillo.com The logo does not want to change.

Target Market(s)

Anyone

Colors

Designer to choose colors to be used in the design.

Requirements
Must have
• You can put the Parlaveo pluggin with the podcast chapters

```html
<!DOCTYPE html>
<html lang="es">
<head>
<meta charset="utf-8">
<title>Before the kettle boils · Podcast de tecnología</title>
<link href="https://fonts.googleapis.com/css2?family=Oswald:wght@400;500;600&family=Open+Sans:wght@400;600&display=swap" rel="stylesheet">
<style>
:root{
  --orange:#f07a14;
  --dark:#232323;
  --darker:#1c1c1c;
  --page:#ececee;
  --card:#ffffff;
  --border:#d9d9dc;
  --text:#555;
  --title:#222;
  --wave:#d4d4d4;
}
*{box-sizing:border-box;margin:0;padding:0}
html,body{width:1200px;height:3727px;overflow:hidden}
body{background:var(--page);font-family:"Open Sans",Arial,sans-serif;color:var(--text);position:relative}

/* header */
.site-header{position:absolute;left:0;top:0;width:1200px;height:132px;background:var(--dark)}
.brand{position:absolute;left:137px;top:18px;display:flex;align-items:center;gap:10px}
.brand-mark{width:40px;height:40px;border-radius:50%;background:var(--orange)}
.brand-name{font-family:"Oswald",sans-serif;font-weight:500;font-size:17px;color:var(--orange);text-transform:uppercase;line-height:1.1}
.brand-tag{position:absolute;left:137px;top:68px;font-family:"Oswald",sans-serif;font-size:12px;color:#ddd;letter-spacing:1px;text-transform:uppercase}
.search{position:absolute;left:850px;top:25px;width:218px;height:37px;background:#333;border:1px solid #444;display:flex;align-items:center;padding-left:14px;gap:10px;color:#ccc;font-size:11px;font-weight:600}
.main-nav{position:absolute;left:700px;top:90px;display:flex}
.main-nav a{font-size:11px;font-weight:600;color:#fff;text-decoration:none;text-transform:uppercase;height:27px;line-height:27px;padding:0 20px}
.main-nav a.active{background:var(--orange)}

/* hero */
.hero{position:absolute;left:0;top:132px;width:1200px;height:457px;background:linear-gradient(120deg,#3b3a3a 0%,#8c7f78 40%,#6f6a6c 60%,#3a3a3e 100%)}
.hero-title{position:absolute;top:125px;width:100%;text-align:center;font-family:"Oswald",sans-serif;font-size:58px;font-weight:500;color:#fff}
.hero-sub{position:absolute;top:200px;width:100%;text-align:center;font-size:19px;color:#fff}
.hero-dots{position:absolute;top:358px;width:100%;display:flex;justify-content:center;gap:16px}
.hero-dots span{width:9px;height:9px;border-radius:50%;background:#fff}
.hero-dots span.current{background:transparent;border:2px solid #fff;width:13px;height:13px;margin-top:-2px}

/* section headings */
.section-title{position:absolute;width:100%;text-align:center;font-family:"Oswald",sans-serif;font-weight:500;font-size:34px;color:var(--orange);text-transform:uppercase}
.section-title::after{content:"";display:block;width:90px;height:2px;background:var(--orange);margin:12px auto 0}
.arrow{position:absolute;font-family:"Oswald",sans-serif;font-size:40px;color:#aaa}

/* grids */
.grid{position:absolute;left:89px;width:1017px;display:grid;gap:22px}
.grid.three{grid-template-columns:repeat(3,1fr)}
.grid.two{grid-template-columns:repeat(2,1fr)}

/* cards */
.post-card{background:var(--card);border:1px solid var(--border);padding:18px 15px 0;height:434px;position:relative}
.post-photo{height:164px;position:relative}
.post-date{position:absolute;right:6px;bottom:6px;background:var(--orange);color:#fff;font-size:8px;font-weight:600;padding:3px 6px}
.post-title{font-family:"Oswald",sans-serif;font-weight:500;font-size:14.5px;line-height:20px;color:var(--title);text-transform:uppercase;margin-top:28px;white-space:nowrap}
.post-excerpt{font-size:11.5px;line-height:19px;margin-top:12px;height:57px;overflow:hidden}
.read-more{display:inline-block;background:var(--orange);color:#fff;font-size:10px;font-weight:600;padding:6px 11px;margin-top:12px;text-transform:uppercase}
.share{position:absolute;left:15px;bottom:24px;display:flex;align-items:center;gap:5px;font-size:10px;color:#333}
.share i{display:block;width:15px;height:15px;border-radius:50%}
.share i:nth-child(1){background:#3aa0e4}.share i:nth-child(2){background:#3b5a98}
.share i:nth-child(3){background:#d84a38}.share i:nth-child(4){background:#1179b3}
.share i:nth-child(5){background:#bbb}.share i:nth-child(6){background:#2d9ad1}
.share i:nth-child(7){background:#4aa9e0}.share i:nth-child(8){background:#4cb050}
.share i:nth-child(9){background:#e04a3f}.share i:nth-child(10){background:#7b9a4a}
.share i:nth-child(11){background:#999}
.share-label{margin-right:8px}

.episode-card{background:var(--card);border:1px solid var(--border);height:435px;position:relative;padding:24px 30px 0}
.episode-card .post-title{margin-top:38px}
.episode-card .post-excerpt{margin-top:14px;height:57px}
.episode-card .share{left:30px;bottom:40px}
.player{height:145px;background:#fff;box-shadow:0 0 0 1px #eee;position:relative;overflow:hidden}
.player.dark{background:#111}
.player-play{position:absolute;left:12px;top:15px;width:44px;height:44px;border-radius:50%;background:#f5b800}
.player-play::after{content:"";position:absolute;left:17px;top:12px;border-left:14px solid #fff;border-top:10px solid transparent;border-bottom:10px solid transparent}
.player-title{position:absolute;left:66px;top:14px;font-size:11px;line-height:15px;color:#333;width:140px}
.player.dark .player-title{color:#eee}
.player-label{position:absolute;left:210px;top:14px;font-size:10px;font-weight:600;color:#333}
.player.dark .player-label{color:#eee}
.player-label b{color:#f5b800}
.player-stats{position:absolute;left:66px;top:50px;display:flex;gap:12px}
.player-stats span{width:8px;height:8px;border-radius:50%;background:#444}
.player.dark .player-stats span{background:#ccc}
.player-times{position:absolute;left:12px;top:74px;width:262px;display:flex;justify-content:space-between;font-size:7px;color:#999}
.player-wave{position:absolute;left:0;bottom:0;width:280px;height:48px;background:repeating-linear-gradient(90deg,var(--wave) 0 2px,transparent 2px 4px);clip-path:polygon(0 60%,8% 30%,15% 55%,22% 20%,30% 50%,38% 35%,46% 60%,55% 25%,63% 45%,72% 30%,80% 55%,88% 35%,100% 50%,100% 100%,0 100%)}
.player.dark .player-wave{background:repeating-linear-gradient(90deg,#777 0 2px,transparent 2px 4px)}
.player-art{position:absolute;right:12px;top:8px;width:134px;height:129px}

.more{position:absolute;left:575px;top:2597px;width:50px;height:50px;border-radius:50%;background:#fff;border:1px solid var(--border);text-align:center;font-size:8px;font-weight:600;color:#555;padding-top:9px}

/* footer */
.site-footer{position:absolute;left:0;top:3322px;width:1200px;height:405px;background:var(--darker)}
.footer-brand{position:absolute;top:45px;width:100%;display:flex;flex-direction:column;align-items:center;gap:8px}
.footer-brand .brand-name{font-size:16px}
.footer-brand .brand-tag{position:static;font-size:11px}
.footer-nav{position:absolute;left:427px;top:190px;width:346px;border-top:1px solid #444;border-bottom:1px solid #444;display:flex;justify-content:space-around;padding:14px 0}
.footer-nav a{color:#fff;font-size:11px;font-weight:600;text-decoration:none;text-transform:uppercase}
.footer-social{position:absolute;top:275px;width:100%;display:flex;justify-content:center;gap:26px}
.footer-social span{width:14px;height:14px;border-radius:50%;background:#ddd}
.footer-rule{position:absolute;left:470px;top:321px;width:260px;height:1px;background:#444}
.copyright{position:absolute;top:345px;width:100%;text-align:center;font-size:11px;color:#aaa}
</style>
</head>
<body>

<header class="site-header">
  <div class="brand"><span class="brand-mark"></span><span class="brand-name">Before the kettle boils</span></div>
  <div class="brand-tag">Podcast de tecnología</div>
  <div class="search">
    <svg width="12" height="12" viewBox="0 0 12 12"><circle cx="5" cy="5" r="3.6" fill="none" stroke="#ccc" stroke-width="1.6"/><line x1="7.6" y1="7.6" x2="11" y2="11" stroke="#ccc" stroke-width="1.6"/></svg>
    SEARCH
  </div>
  <nav class="main-nav">
    <a class="active" href="#">Home</a><a href="#">About us</a><a href="#">Latest post</a><a href="#">Contact us</a>
  </nav>
</header>

<section class="hero" role="img" aria-label="Photo of a person holding a phone and listening with earphones">
  <h1 class="hero-title">PODCAST</h1>
  <p class="hero-sub">Lorem Ipsum is simply dummy text of the printing</p>
  <div class="hero-dots"><span></span><span class="current"></span><span></span><span></span><span></span></div>
</section>

<h2 class="section-title" style="top:632px">Featured Posts</h2>

<div class="grid three" style="top:765px">
  <article class="post-card">
    <div class="post-photo" role="img" aria-label="Photo of a woman using a tablet" style="background:linear-gradient(135deg,#6c7a80,#c9c9c4)"><span class="post-date">May 22,2017</span></div>
    <h3 class="post-title">Cambio de logo</h3>
    <p class="post-excerpt">¿Salta a la vista no?, pues sí, renovamos diseño del logo y algo en la web. Aquí los cambios irán poco a poco pero procuraré dejar...</p>
    <span class="read-more">Read more</span>
    <div class="share"><span class="share-label">Comparte :</span><i></i><i></i><i></i><i></i><i></i><i></i><i></i><i></i><i></i><i></i><i></i></div>
  </article>
  <article class="post-card">
    <div class="post-photo" role="img" aria-label="Photo of a microphone in front of a screen with audio waves" style="background:linear-gradient(135deg,#3a2f2a,#3f7fb6)"><span class="post-date">May 22,2017</span></div>
    <h3 class="post-title">¿Te gustan las series?¿Conoces cinetto.tv?</h3>
    <p class="post-excerpt">Hoy capítulo dedicado a los amantes de las series y las películas. Se trata del servicio de vídeo en streaming de la web cinetto.tv portal dedicado...</p>
    <span class="read-more">Read more</span>
    <div class="share"><span class="share-label">Comparte :</span><i></i><i></i><i></i><i></i><i></i><i></i><i></i><i></i><i></i><i></i><i></i></div>
  </article>
  <article class="post-card">
    <div class="post-photo" role="img" aria-label="Photo of a wooden desk with a phone, headphones and coffee" style="background:linear-gradient(135deg,#8a5636,#c79066)"><span class="post-date">May 22,2017</span></div>
    <h3 class="post-title">Un anuncio y una prueba</h3>
    <p class="post-excerpt">Sí, lo sé ha vuelto a pasar, mucho tiempo desde la última publicación. Esto lo tengo muy abandonado y no hay excusa, me da pena pero...</p>
    <span class="read-more">Read more</span>
    <div class="share"><span class="share-label">Comparte :</span><i></i><i></i><i></i><i></i><i></i><i></i><i></i><i></i><i></i><i></i><i></i></div>
  </article>
</div>

<div class="grid two" style="top:1223px">
  <article class="episode-card">
    <div class="player">
      <span class="player-play"></span><span class="player-title">¿Te gustan las series? ¿Conoces cinetto.tv?</span>
      <span class="player-label"><b>●</b> Parlaveo</span>
      <div class="player-stats"><span></span><span></span><span></span></div>
      <div class="player-times"><span>00:00</span><span>13:55</span></div>
      <div class="player-wave"></div>
      <div class="player-art" role="img" aria-label="Collage of series posters" style="background:linear-gradient(135deg,#2a2a30,#6a4e3c)"></div>
    </div>
    <h3 class="post-title">¿Te gustan las series?¿Conoces cinetto.tv?</h3>
    <p class="post-excerpt">Hoy capítulo dedicado a los amantes de las series y las películas. Se trata del servicio de vídeo en streaming de la web cinetto.tv portal dedicado</p>
    <span class="read-more">Read more</span>
    <div class="share"><span class="share-label">Comparte</span><i></i><i></i><i></i><i></i><i></i><i></i><i></i><i></i><i></i><i></i><i></i></div>
  </article>
  <article class="episode-card">
    <div class="player">
      <span class="player-play"></span><span class="player-title">Un anuncio y una prueba</span>
      <span class="player-label"><b>●</b> Parlaveo</span>
      <div class="player-stats"><span></span><span></span><span></span></div>
      <div class="player-times"><span>00:00</span><span>06:12</span></div>
      <div class="player-wave"></div>
      <div class="player-art" role="img" aria-label="Episode cover artwork in black and white" style="background:#111"></div>
    </div>
    <h3 class="post-title">Un anuncio y una prueba</h3>
    <p class="post-excerpt">Sí, lo sé ha vuelto a pasar, mucho tiempo desde la última publicación. Esto lo tengo muy abandonado y no hay excusa, me da pena pero es cierto, por gandulería o por motivos de tiempo no le he dedicado la atención que merece.</p>
    <span class="read-more">Read more</span>
    <div class="share"><span class="share-label">Comparte</span><i></i><i></i><i></i><i></i><i></i><i></i><i></i><i></i><i></i><i></i><i></i></div>
  </article>
  <article class="episode-card">
    <div class="player">
      <span class="player-play"></span><span class="player-title">Seguridad en tu Mail</span>
      <span class="player-label"><b>●</b> Parlaveo</span>
      <div class="player-stats"><span></span><span></span><span></span></div>
      <div class="player-times"><span>00:00</span><span>09:15</span></div>
      <div class="player-wave"></div>
      <div class="player-art" role="img" aria-label="Episode cover artwork about email security" style="background:#3d3f72"></div>
    </div>
    <h3 class="post-title">Seguridad en tu mail</h3>
    <p class="post-excerpt">Hoy capítulo dedicado a los amantes de las series y las películas. Se trata del servicio de vídeo en streaming de la web cinetto.tv portal dedicado</p>
    <span class="read-more">Read more</span>
    <div class="share"><span class="share-label">Comparte</span><i></i><i></i><i></i><i></i><i></i><i></i><i></i><i></i><i></i><i></i><i></i></div>
  </article>
  <article class="episode-card">
    <div class="player">
      <span class="player-play"></span><span class="player-title">Kumo KumoTab 2, calidad precio insuperable</span>
      <span class="player-label"><b>●</b> Parlaveo</span>
      <div class="player-stats"><span></span><span></span><span></span></div>
      <div class="player-times"><span>00:00</span><span>23:31</span></div>
      <div class="player-wave"></div>
      <div class="player-art" role="img" aria-label="Episode cover artwork about a tablet" style="background:#f36b21"></div>
    </div>
    <h3 class="post-title">Kumo KumoTab 2, calidad precio insuperable</h3>
    <p class="post-excerpt">Con un poco de retraso publicamos el post del podcast de la tableta de Kumo. Tablets que como viene siendo habitual de la marca, da mucho más de lo que cuesta.</p>
    <span class="read-more">Read more</span>
    <div class="share"><span class="share-label">Comparte</span><i></i><i></i><i></i><i></i><i></i><i></i><i></i><i></i><i></i><i></i><i></i></div>
  </article>
  <article class="episode-card">
    <div class="player">
      <span class="player-play"></span><span class="player-title">Notaria, así lo hago yo</span>
      <span class="player-label"><b>●</b> Parlaveo</span>
      <div class="player-stats"><span></span><span></span><span></span></div>
      <div class="player-times"><span>00:00</span><span>20:05</span></div>
      <div class="player-wave"></div>
      <div class="player-art" role="img" aria-label="Episode cover artwork about a notes app" style="background:#6ab63a"></div>
    </div>
    <h3 class="post-title">Notaria, así lo hago yo</h3>
    <p class="post-excerpt">En este podcast os hablo de mi uso particular de Notaria, con pros y contras, cómo organizo, etc. Intentaré hacer por aquí un resumen de lo comentado en el podcast.</p>
    <span class="read-more">Read more</span>
    <div class="share"><span class="share-label">Comparte</span><i></i><i></i><i></i><i></i><i></i><i></i><i></i><i></i><i></i><i></i><i></i></div>
  </article>
  <article class="episode-card">
    <div class="player dark">
      <span class="player-play"></span><span class="player-title">Podcast futuros, Parlaveo, serie recomendada</span>
      <span class="player-label"><b>●</b> Parlaveo</span>
      <div class="player-stats"><span></span><span></span><span></span></div>
      <div class="player-times"><span>00:00</span><span>13:20</span></div>
      <div class="player-wave"></div>
      <div class="player-art" role="img" aria-label="Episode cover artwork of an underwater scene" style="background:linear-gradient(135deg,#0b2a3a,#3b8fa8)"></div>
    </div>
    <h3 class="post-title">Podcast futuros, Parlaveo, serie recomendada</h3>
    <p class="post-excerpt">Podcast de hoy variado, un adelanto de uno o una serie (ya veremos) de podcast que voy a grabar en un futuro, opinión de los nuevos planes de precios de Parlaveo y la recomendación de una serie The Tin Orchard.</p>
    <span class="read-more">Read more</span>
    <div class="share"><span class="share-label">Comparte</span><i></i><i></i><i></i><i></i><i></i><i></i><i></i><i></i><i></i><i></i><i></i></div>
  </article>
</div>

<div class="more">MORE<br>
  <svg width="14" height="10" viewBox="0 0 14 10"><polyline points="2,2 7,7 12,2" fill="none" stroke="#555" stroke-width="2"/></svg>
</div>

<h2 class="section-title" style="top:2710px">Recent Posts</h2>
<span class="arrow" style="left:443px;top:2704px">‹</span>
<span class="arrow" style="left:724px;top:2704px">›</span>

<div class="grid three" style="top:2830px">
  <article class="post-card">
    <div class="post-photo" role="img" aria-label="Photo of a studio microphone" style="background:linear-gradient(135deg,#1d1d1d,#6a6a6a)"><span class="post-date">May 22,2017</span></div>
    <h3 class="post-title">Cambio de logo</h3>
    <p class="post-excerpt">¿Salta a la vista no?, pues sí, renovamos diseño del logo y algo en la web. Aquí los cambios irán poco a poco pero procuraré dejar...</p>
    <span class="read-more">Read more</span>
    <div class="share"><span class="share-label">Comparte :</span><i></i><i></i><i></i><i></i><i></i><i></i><i></i><i></i><i></i><i></i><i></i></div>
  </article>
  <article class="post-card">
    <div class="post-photo" role="img" aria-label="Photo of a person working on a laptop" style="background:linear-gradient(135deg,#a4572e,#3a3a3a)"><span class="post-date">May 22,2017</span></div>
    <h3 class="post-title">¿Te gustan las series?¿Conoces cinetto.tv?</h3>
    <p class="post-excerpt">Hoy capítulo dedicado a los amantes de las series y las películas. Se trata del servicio de vídeo en streaming de la web cinetto.tv portal dedicado al...</p>
    <span class="read-more">Read more</span>
    <div class="share"><span class="share-label">Comparte :</span><i></i><i></i><i></i><i></i><i></i><i></i><i></i><i></i><i></i><i></i><i></i></div>
  </article>
  <article class="post-card">
    <div class="post-photo" role="img" aria-label="Photo of a phone with a music app and a laptop" style="background:linear-gradient(135deg,#e8e8e8,#4a4a4a)"><span class="post-date">May 22,2017</span></div>
    <h3 class="post-title">Un anuncio y una prueba</h3>
    <p class="post-excerpt">Sí, lo sé ha vuelto a pasar, mucho tiempo desde la última publicación. Esto lo tengo muy abandonado y no hay excusa, me da pena pero...</p>
    <span class="read-more">Read more</span>
    <div class="share"><span class="share-label">Comparte :</span><i></i><i></i><i></i><i></i><i></i><i></i><i></i><i></i><i></i><i></i><i></i></div>
  </article>
</div>

<footer class="site-footer">
  <div class="footer-brand">
    <span class="brand-mark"></span>
    <span class="brand-name">Before the kettle boils</span>
    <span class="brand-tag">Podcast de tecnología</span>
  </div>
  <nav class="footer-nav"><a href="#">Home</a><a href="#">About us</a><a href="#">Latest post</a><a href="#">Contact us</a></nav>
  <div class="footer-social"><span></span><span></span><span></span><span></span></div>
  <div class="footer-rule"></div>
  <p class="copyright">Copyright © 2017 All Rights Reserved</p>
</footer>

</body>
</html>
```